Web Design For Staffing Company

We need a homepage web design for a technical staffing company.

Please see attached brief for project details.

please make the site modern with bold colors while matching the logo

Be sure to read the attached breif in full beforehand.

Target Market(s)

technical companies looking to hire talent

Industry/Entity Type

Staffing

Number of Pages Required

1 page

Font styles to use
Sans Serif

```html
<!DOCTYPE html>
<html lang="en">
<head>
<meta charset="utf-8">
<title>Vantora Staffing — Technical Staffing</title>
<link rel="stylesheet" href="https://fonts.googleapis.com/css2?family=Mulish:ital,wght@0,400;0,600;0,700;0,800;1,400&family=Oswald:wght@400&display=swap">
<style>
:root{
  --blue:#1b8fd0;
  --blue-dark:#1477b0;
  --ink:#111;
  --text:#333;
  --muted:#555;
  --grey-bg:#f2f2f2;
  --white:#fff;
  --black:#050608;
}
*{box-sizing:border-box;margin:0;padding:0}
html,body{width:1200px;height:3661px;overflow:hidden}
body{position:relative;font-family:'Mulish',sans-serif;color:var(--text);background:var(--white)}
.abs{position:absolute}
.btn{position:absolute;display:flex;align-items:center;justify-content:center;font-family:'Mulish',sans-serif;font-weight:700;font-size:13px;letter-spacing:.5px;text-transform:uppercase;text-decoration:none;gap:6px}
.btn-blue{background:var(--blue);color:var(--white)}
.btn-black{background:var(--ink);color:var(--white)}
.btn-white{background:var(--white);color:var(--blue)}

/* header */
.site-header{position:absolute;left:0;top:0;width:1200px;height:98px;background:var(--white)}
.brand{position:absolute;left:142px;top:30px;font-weight:800;font-size:26px;color:var(--blue-dark);display:flex;align-items:center;gap:10px}
.brand-square{width:22px;height:22px;background:var(--blue-dark)}
.main-nav a{position:absolute;top:41px;font-size:13px;color:#222;text-decoration:none}
.main-nav a.active{color:var(--blue)}
.search{position:absolute;left:867px;top:28px;width:192px;height:40px;border:1px solid #ddd;font-size:11px;color:#777;padding:13px 16px}
.search svg{position:absolute;right:12px;top:11px}

/* hero */
.hero{position:absolute;left:0;top:98px;width:1200px;height:592px;background:linear-gradient(90deg,#020407 0%,#08121d 50%,#0d2035 75%,#06101a 100%)}
.hero-art{position:absolute;left:620px;top:40px;width:400px;height:520px;background:radial-gradient(ellipse at 55% 40%,rgba(120,150,180,.55),rgba(30,50,70,.2) 60%,transparent 75%)}
.hero h1{position:absolute;left:142px;top:178px;font-family:'Oswald',sans-serif;font-weight:400;font-size:35px;line-height:48px;color:var(--white);width:480px}
.hero h1 span{display:block}

/* intro */
.intro{position:absolute;left:230px;top:766px;width:740px;text-align:center;font-size:18px;line-height:31px;color:#333}
.intro mark{background:var(--blue);color:var(--white);padding:2px 8px;font-weight:600}

/* feature band */
.band{position:absolute;left:0;top:936px;width:1200px;height:378px;background:linear-gradient(90deg,#1884c4,#2298d8 50%,#1884c4)}
.card{position:absolute;top:1021px;width:432px;height:617px;background:var(--white);box-shadow:0 2px 14px rgba(0,0,0,.08)}
.card-photo{width:432px;height:293px}
.card-body{padding:30px 32px;font-size:12.5px;line-height:22px;color:#333}
.card-body h2{font-size:18px;font-weight:700;color:#111;margin-bottom:10px;letter-spacing:.3px}
.card-body h2 em{font-style:normal;color:var(--blue)}
.card-body p{margin-bottom:10px}
.card-body p.lead{font-size:13.5px}

/* testimonials */
.section-title{position:absolute;left:0;width:1200px;text-align:center;font-size:28px;font-weight:600;color:#111;letter-spacing:.5px}
.section-title em{font-style:normal;color:var(--blue)}
.quote{position:absolute;left:285px;top:1794px;width:630px;text-align:center;font-style:italic;font-size:15.5px;line-height:26.5px;color:#222}
.divider{position:absolute;left:356px;top:1922px;width:489px;height:1px;background:#bbb}
.name{position:absolute;left:0;width:1200px;text-align:center}

/* blogs */
.blogs{position:absolute;left:0;top:2100px;width:1200px;height:691px;background:var(--grey-bg)}
.post{position:absolute;top:2237px;width:293px;height:394px;background:var(--white);box-shadow:0 2px 8px rgba(0,0,0,.05)}
.post-photo{height:177px}
.post-body{padding:16px 16px;font-size:12px;line-height:22px;color:#555}
.post-meta{display:flex;justify-content:space-between;font-size:13px;font-weight:600;color:#666}
.post-meta .date{color:var(--blue)}
.post-body h3{font-size:14px;font-weight:700;color:#222;line-height:21px;margin:6px 0 8px}
.post-body a{color:var(--blue);font-weight:700;font-size:12px;text-decoration:underline}
.arrow{position:absolute;top:2393px;width:42px;height:42px;border-radius:50%;background:var(--white);box-shadow:0 2px 8px rgba(0,0,0,.12);display:flex;align-items:center;justify-content:center}

/* cta */
.cta{position:absolute;top:2877px;width:443px;height:281px;padding:0 34px}
.cta-blue{left:141px;background:linear-gradient(120deg,#1f97d6,#1783c2)}
.cta-dark{left:616px;background:linear-gradient(120deg,#151b22,#2a3440)}
.cta svg{position:absolute;left:34px;top:38px}
.cta h2{position:absolute;left:34px;top:130px;font-size:23px;font-weight:700;line-height:29px;color:var(--white)}

/* footer */
.footer{position:absolute;left:0;top:3240px;width:1200px;height:421px}
.footer h4{position:absolute;top:156px;font-size:16px;font-weight:700;color:var(--white);letter-spacing:.5px}
.footer p{position:absolute;top:184px;font-size:12px;line-height:18px;color:#ddd}
.footer .btn{top:281px;height:38px;font-size:12px;font-weight:600}
.footer-brand{position:absolute;left:860px;top:215px;font-weight:800;font-size:30px;color:#d8d8d8;display:flex;align-items:center;gap:12px}
.legal{position:absolute;left:0;top:379px;width:1200px;height:42px;background:var(--blue)}
.legal p{position:absolute;left:142px;top:13px;font-size:12px;color:var(--white)}
.social{position:absolute;top:9px;width:24px;height:24px;border:1.5px solid var(--white);border-radius:50%}
</style>
</head>
<body>

<header class="site-header">
  <div class="brand"><span class="brand-square"></span>Vantora Staffing</div>
  <nav class="main-nav">
    <a class="active" style="left:444px">HOME</a>
    <a style="left:509px">ABOUT</a>
    <a style="left:582px">JOB SEEKERS</a>
    <a style="left:698px">CLIENTS</a>
    <a style="left:778px">CONTACT</a>
  </nav>
  <div class="search">Search
    <svg width="17" height="17" viewBox="0 0 17 17"><circle cx="7" cy="7" r="5" fill="none" stroke="#1b8fd0" stroke-width="2.2"/><line x1="11" y1="11" x2="15.5" y2="15.5" stroke="#1b8fd0" stroke-width="2.4"/></svg>
  </div>
</header>

<section class="hero">
  <div class="hero-art" role="img" aria-label="Hand touching a network of HR and recruiting icons"></div>
  <h1><span>The Right People For The Right Jobs!</span><span>Bridging the talent gap in Technical</span><span>Staffing</span></h1>
  <a class="btn btn-white" style="left:142px;top:360px;width:141px;height:44px">Hire Talent</a>
  <a class="btn btn-blue" style="left:303px;top:360px;width:141px;height:44px">Get Hired</a>
</section>

<p class="intro"><mark>Vantora Staffing</mark> is a National Technical Staffing and Recruiting Solutions Provider founded in2013 focused on matching contract and full time Engineering and IT professionals with new andexciting employment opportunities!</p>

<div class="band" role="img" aria-label="Blue toned office team background"></div>

<article class="card" style="left:142px">
  <div class="card-photo" role="img" aria-label="Team meeting around a conference table" style="background:linear-gradient(135deg,#c9d6e0,#7d8e9c 55%,#3e4a56)"></div>
  <div class="card-body">
    <h2>SIMPLY SAID... <em>WE LOVE TO RECRUIT!</em></h2>
    <p class="lead">It's our passion and we take it very seriously!</p>
    <p>It is not easy for JOB SEEKERS to put their job search efforts and trust in the hands of someone else, especially when there are so many Staffing Firms to choose from.</p>
    <p>So how do you know you are choosing the best Staffing Representation possible?</p>
  </div>
  <a class="btn btn-black" style="left:31px;top:543px;width:124px;height:39px">Learn More</a>
  <a class="btn btn-blue" style="left:174px;top:543px;width:122px;height:39px">View Jobs</a>
</article>

<article class="card" style="left:627px">
  <div class="card-photo" role="img" aria-label="Colleagues talking at an office desk" style="background:linear-gradient(135deg,#dfe6ea,#98a6b0 55%,#4b5660)"></div>
  <div class="card-body" style="font-size:12px;line-height:23.5px">
    <p style="margin-bottom:0">Are you responsible for Technical Staffing within your organization?</p>
    <p style="margin-bottom:0">Are you satisfied with your current Supplier(s)' overall performance?</p>
    <p style="margin-bottom:0">Does it appear they identify potential Candidate(s) based purely on "buzz-word" searches?</p>
    <p>Is it evident they just do not grasp the scope and responsibilities of your technical staffing need(s)?</p>
  </div>
  <a class="btn btn-black" style="left:32px;top:543px;width:124px;height:39px">Learn More</a>
  <a class="btn btn-blue" style="left:174px;top:543px;width:124px;height:39px">Hire Talent</a>
</article>

<h2 class="section-title" style="top:1716px">CUSTOMER <em>TESTIMONIALS</em></h2>
<svg class="abs" style="left:230px;top:1770px" width="58" height="42" viewBox="0 0 58 42"><path d="M24 4C12 6 4 14 4 26a12 12 0 1 0 12-12c1-4 4-7 8-8z M54 4C42 6 34 14 34 26a12 12 0 1 0 12-12c1-4 4-7 8-8z" fill="none" stroke="#7cc0e8" stroke-width="3"/></svg>
<p class="quote">Marcus Hale is an excellent recruiter. He is articulate, honest, has a good nature and is aneffective information conduit between his clients and candidates. He gave me the feeling he is there for the big picture desiring to forge a future relationship that will be mutually beneficial toboth of us.</p>
<svg class="abs" style="left:899px;top:1882px" width="58" height="40" viewBox="0 0 58 42"><path d="M4 38c12-2 20-10 20-22a12 12 0 1 0-12 12c-1 4-4 7-8 8z M34 38c12-2 20-10 20-22a12 12 0 1 0-12 12c-1 4-4 7-8 8z" fill="none" stroke="#7cc0e8" stroke-width="3"/></svg>
<div class="divider"></div>
<svg class="abs" style="left:593px;top:1922px" width="14" height="8"><path d="M0 0h14L7 7z" fill="#bbb"/></svg>
<p class="name" style="top:1947px;font-size:15px;font-weight:600;color:#111">SAM R</p>
<p class="name" style="top:1970px;font-size:12px;color:#333">Electrical Test Engineer in the Automotive Sector</p>
<svg class="abs" style="left:547px;top:1995px" width="106" height="20" viewBox="0 0 106 20">
  <g fill="#f6b500"><path id="s" d="M9 1l2.5 5.3 5.8.7-4.3 4 1.1 5.8L9 14l-5.1 2.8L5 11 .7 7l5.8-.7z"/><use href="#s" x="22"/><use href="#s" x="44"/><use href="#s" x="66"/><use href="#s" x="88"/></g>
</svg>

<section class="blogs"></section>
<h2 class="section-title" style="top:2174px">LATEST <em>BLOGS</em></h2>

<article class="post" style="left:141px">
  <div class="post-photo" role="img" aria-label="Black and white portrait with a quote about technology" style="background:linear-gradient(90deg,#bdbdbd,#555 45%,#111)"></div>
  <div class="post-body">
    <div class="post-meta"><span class="date">June 19, 2019</span><span>by vantorastaffing</span></div>
    <h3>Tips for Spotting a U.S. Recession Before It Becomes Official</h3>
    <p>As the U.S. nears a record-long expansion in July, the conversation is increasingly turning to when it will all end.</p>
    <a>READ MORE</a>
  </div>
</article>
<article class="post" style="left:454px">
  <div class="post-photo" role="img" aria-label="Woman working on a laptop" style="background:linear-gradient(120deg,#e8e6e2,#9a948e 55%,#2f3a4a)"></div>
  <div class="post-body">
    <div class="post-meta"><span class="date">June 17, 2019</span><span>by vantorastaffing</span></div>
    <h3>Ways To Make The Most Of The Hot Job Market</h3>
    <p>This is the tightest labor market I can remember. Unemployment is at a 50-year low and wage growth is at 3.2%," said</p>
    <a>READ MORE</a>
  </div>
</article>
<article class="post" style="left:766px">
  <div class="post-photo" role="img" aria-label="Business handshake over a desk" style="background:linear-gradient(120deg,#8fb0cc,#3f6a92 55%,#1c3550)"></div>
  <div class="post-body">
    <div class="post-meta"><span class="date">June 6, 2019</span><span>by vantorastaffing</span></div>
    <h3>Back To Basics: Meeting Employees' Needs To Improve Organizational...</h3>
    <p>The benefits of employee satisfaction are well-established, so HR professionals and leaders across all industries spend a</p>
    <a>READ MORE</a>
  </div>
</article>
<div class="arrow" style="left:69px"><svg width="18" height="14" viewBox="0 0 18 14"><path d="M17 7H2M7 1L1 7l6 6" fill="none" stroke="#7cc0e8" stroke-width="2"/></svg></div>
<div class="arrow" style="left:1088px"><svg width="18" height="14" viewBox="0 0 18 14"><path d="M1 7h15M11 1l6 6-6 6" fill="none" stroke="#1b8fd0" stroke-width="2"/></svg></div>
<a class="btn btn-blue" style="left:546px;top:2668px;width:108px;height:38px">View All</a>

<section class="cta cta-blue" role="img" aria-label="Smiling professional team background">
  <svg width="84" height="76" viewBox="0 0 84 76" fill="none" stroke="#fff" stroke-width="2.5"><circle cx="42" cy="16" r="10"/><path d="M24 56c0-12 8-20 18-20s18 8 18 20v14H24z"/><circle cx="18" cy="24" r="8"/><path d="M4 62c0-10 6-16 14-16"/><circle cx="66" cy="24" r="8"/><path d="M80 62c0-10-6-16-14-16"/></svg>
  <h2>Looking For Career-minded<br>Candidates?</h2>
  <a class="btn btn-black" style="left:34px;top:206px;width:162px;height:38px">Request Talent</a>
</section>
<section class="cta cta-dark" role="img" aria-label="Smiling office workers background">
  <svg width="80" height="76" viewBox="0 0 80 76" fill="none" stroke="#fff" stroke-width="2.5"><circle cx="30" cy="18" r="12"/><path d="M6 72V54c0-10 10-18 24-18 8 0 14 3 18 7"/><rect x="44" y="48" width="30" height="22"/><path d="M54 48v-5h10v5M44 56h30"/></svg>
  <h2>Looking For Career-minded<br>Candidates?</h2>
  <a class="btn btn-blue" style="left:32px;top:206px;width:131px;height:38px">Search Jobs</a>
</section>

<footer class="footer">
  <svg class="abs" style="left:0;top:0" width="1200" height="379" viewBox="0 0 1200 379">
    <path d="M0 120 Q600 -30 1200 120 V379 H0Z" fill="#050608"/>
    <path d="M0 120 Q600 -30 1200 120" fill="none" stroke="#1b8fd0" stroke-width="4"/>
  </svg>
  <h4 style="left:142px">FIND JOBS</h4>
  <p style="left:142px;width:170px">Search Our extensive<br>list of available jobs to find<br>your match.</p>
  <h4 style="left:337px">REQUEST AN EMPLOYEE</h4>
  <p style="left:338px;width:210px">We're here to provide the people<br>you need to get work done.</p>
  <h4 style="left:596px">GET IN TOUCH</h4>
  <svg class="abs" style="left:592px;top:190px" width="10" height="14" viewBox="0 0 10 14"><path d="M5 0a5 5 0 0 0-5 5c0 4 5 9 5 9s5-5 5-9a5 5 0 0 0-5-5z" fill="#1b8fd0"/><circle cx="5" cy="5" r="2" fill="#050608"/></svg>
  <p style="left:613px">120 Harbor Lane, Bldg. 2,<br>3rd floor Millbrook,<br>MA 01990</p>
  <svg class="abs" style="left:592px;top:250px" width="12" height="12" viewBox="0 0 12 12"><path d="M2 0l3 3-1.5 2a8 8 0 0 0 3.5 3.5L9 7l3 3-2 2C5 12 0 7 0 2z" fill="#1b8fd0"/></svg>
  <p style="left:613px;top:248px">555-014-2870</p>
  <a class="btn btn-blue" style="left:142px;width:135px">
    <svg width="13" height="13" viewBox="0 0 17 17"><circle cx="7" cy="7" r="5" fill="none" stroke="#fff" stroke-width="2.4"/><line x1="11" y1="11" x2="15.5" y2="15.5" stroke="#fff" stroke-width="2.6"/></svg>Search Now</a>
  <a class="btn btn-blue" style="left:338px;width:136px">
    <svg width="12" height="13" viewBox="0 0 12 13"><circle cx="6" cy="3.5" r="3.2" fill="#fff"/><path d="M0 13c0-4 3-6 6-6s6 2 6 6z" fill="#fff"/></svg>Start Today</a>
  <a class="btn btn-blue" style="left:593px;width:135px">
    <svg width="14" height="10" viewBox="0 0 14 10"><rect width="14" height="10" fill="#fff"/><path d="M0 0l7 6 7-6" fill="none" stroke="#1b8fd0" stroke-width="1.4"/></svg>Contact Us</a>
  <div class="footer-brand"><span style="width:30px;height:30px;background:#d8d8d8"></span>Vantora Staffing</div>
  <div class="legal">
    <p>Copyright © 2020 Vantora Staffing. All Rights Reserved.</p>
    <span class="social" style="left:964px" aria-label="Social profile"></span>
    <span class="social" style="left:999px" aria-label="Social profile"></span>
    <span class="social" style="left:1034px" aria-label="Social profile"></span>
  </div>
</footer>

</body>
</html>
```